International business needs business cards

Our company, DRV Ventures Inc. is in the business of supplying a range construction products with particular emphasis on CEMENT. We have developed our own brand - TORVAN SUPPLIES - with which to infiltrate the market. We are launching our brand of cement (TORVAN Type IS Cement) into the Caribbean which is unlike anything this market has ever seen. A monopoly has existed here for the past 60-odd years and the market has now opened to allow the importation of other brands and consumers are anxious and ready for change/improvement. We are very excited to be launching and want to make a great first impression. We will be conducting workshops and seminars (from government level to the hardware store owners) and we want our business card to give us the strong, confident introduction that we need.

Target Market(s)

construction; builders; engineers; home owners

Industry/Entity Type

Construction

Contact Information for Business Card

Marisol Depree
CEO
cell # 1 555 4180736
Ground floor,Lindell Plaza Suite 2734
George Town,Grand Cayman
Cayman Islands,KY1-4823
EMAIL: m.depree@drvventuresinc.example
web site drvventuresinc.example

COMPANY: skype info drv.ventures.example

second card
Yvette Brannock-Depree
CFO
CELL# 1 555 607 3941
George Town,Grand Cayman
Cayman Islands,KY1-4823
EMAIL: y.brannockdepree@drvventuresinc.example
website drvventuresinc.example

Requirements
Must have
• Business cards must display BOTH logos - DRV is the company and TORVAN is the brand.

```html
<!DOCTYPE html>
<html lang="en">
<head>
<meta charset="utf-8">
<title>DRV Ventures Inc. — Business Card</title>
<link rel="stylesheet" href="https://fonts.googleapis.com/css2?family=Open+Sans:wght@400;600;700&display=swap">
<style>
  :root {
    --stage: #e9e7e4;
    --card: #ffffff;
    --brand-red: #8b1a22;
    --brand-red-light: #a9464d;
    --ink: #2b2b2b;
    --ink-soft: #555555;
    --rule: #9a9a9a;
    --font: "Open Sans", Arial, sans-serif;
  }
  * { box-sizing: border-box; margin: 0; padding: 0; }
  html, body {
    width: 1200px; height: 843px; overflow: hidden;
    background: var(--stage);
    font-family: var(--font);
    color: var(--ink);
  }
  .stage {
    width: 1200px; height: 843px;
    display: flex; flex-direction: column;
    align-items: center; justify-content: center; gap: 36px;
  }
  .card {
    width: 640px; height: 366px;
    background: var(--card);
    position: relative; overflow: hidden;
    box-shadow: 0 6px 18px rgba(0,0,0,.18);
  }

  /* Back face */
  .card--back {
    display: flex; flex-direction: column;
    align-items: center; justify-content: center;
    background: linear-gradient(135deg, #ffffff 0%, #f1f1f1 100%);
  }
  .company-mark {
    display: flex; align-items: center; gap: 14px;
  }
  .company-mark__square {
    width: 58px; height: 58px; background: var(--brand-red);
  }
  .company-mark__name {
    font-weight: 700; font-size: 34px; color: var(--ink);
    letter-spacing: .5px;
  }
  .card--back .web {
    position: absolute; bottom: 56px; left: 0; right: 0;
    text-align: center; font-size: 15px; letter-spacing: 3px;
    color: var(--ink-soft);
  }

  /* Front face */
  .card__band {
    position: absolute; top: 0; left: 0; bottom: 0; width: 256px;
    background: linear-gradient(200deg, var(--brand-red) 0%, var(--brand-red) 55%, var(--brand-red-light) 100%);
    display: flex; align-items: center; justify-content: center; gap: 12px;
  }
  .brand-mark__circle {
    width: 16px; height: 16px; border-radius: 50%; background: #ffffff;
  }
  .brand-mark__name {
    font-weight: 700; font-size: 30px; color: #ffffff; letter-spacing: 2px;
  }
  .contact {
    position: absolute; top: 52px; left: 300px; right: 36px;
  }
  .contact__name {
    font-weight: 700; font-size: 23px; color: var(--brand-red); line-height: 1.1;
  }
  .contact__role {
    font-size: 13px; color: var(--ink); margin-top: 2px;
  }
  .divider {
    border: 0; border-top: 2px dotted var(--rule);
    margin: 12px 0 14px;
  }
  .contact__address {
    font-style: normal; font-size: 15px; line-height: 1.3; color: var(--ink-soft);
  }
  .contact__lines { list-style: none; font-size: 15px; color: var(--ink-soft); }
  .contact__lines li {
    display: flex; align-items: center; gap: 9px; line-height: 1.45;
  }
  .icon { width: 14px; height: 14px; flex: none; }
</style>
</head>
<body>
<main class="stage">

  <section class="card card--back" aria-label="Business card back">
    <div class="company-mark">
      <span class="company-mark__square"></span>
      <span class="company-mark__name">DRV Ventures Inc.</span>
    </div>
    <p class="web">www.drvventuresinc.example</p>
  </section>

  <section class="card card--front" aria-label="Business card front">
    <div class="card__band">
      <span class="brand-mark__circle"></span>
      <span class="brand-mark__name">TORVAN</span>
    </div>

    <div class="contact">
      <h1 class="contact__name">Marisol Depree</h1>
      <p class="contact__role">CEO</p>
      <hr class="divider">
      <address class="contact__address">
        Ground floor<br>
        Lindell Plaza Suite 2734<br>
        George Town,Grand Cayman<br>
        Cayman Islands,KY1-4823
      </address>
      <hr class="divider">
      <ul class="contact__lines">
        <li>
          <svg class="icon" viewBox="0 0 14 14" aria-hidden="true">
            <rect x="3" y="0.5" width="8" height="13" rx="1.5" fill="none" stroke="#8b1a22" stroke-width="1.5"/>
            <circle cx="7" cy="11" r="0.9" fill="#8b1a22"/>
          </svg>
          1 555 4180736
        </li>
        <li>
          <svg class="icon" viewBox="0 0 14 14" aria-hidden="true">
            <rect x="0" y="2" width="14" height="10" fill="#8b1a22"/>
            <path d="M0.5 2.5 L7 8 L13.5 2.5" fill="none" stroke="#ffffff" stroke-width="1.2"/>
          </svg>
          m.depree@drvventuresinc.example
        </li>
        <li>
          <svg class="icon" viewBox="0 0 14 14" aria-hidden="true">
            <circle cx="7" cy="7" r="6.5" fill="#8b1a22"/>
            <ellipse cx="7" cy="7" rx="2.8" ry="6.5" fill="none" stroke="#ffffff" stroke-width="1"/>
            <line x1="0.5" y1="7" x2="13.5" y2="7" stroke="#ffffff" stroke-width="1"/>
          </svg>
          www.drvventuresinc.example
        </li>
      </ul>
    </div>
  </section>

</main>
</body>
</html>
```